Foot and ankle surgeon requires a website design

I need a website where prospective and established patients can obtain information and then direct them to making appointments. My practice is a highly professional surgical practice specialising in surgery to the foot and ankle. My title is Mr Colin Brasket, Podiatric Foot & Ankle Surgeon. My qualifications are: BSc MSc FACPS
The practice website will require information on: Locations, phone numbers to make appointments, general background on podiatric surgery,
I would like to include information on: my hospital appointments, surgical fellowships held, training programs undertaken, association memberships, publications written, links to useful websites
A page dedicated to common foot conditions would be useful and also a page with referral information including an online registration section that will be sent direct to the receptionist.
Examples of similar websites include:
http://www.dorvelquintaro.com.au/
http://www.haldenfootsurgeon.com.au/
I will provide files on logo, self photos and my personal training history etc.
Also if there is going to be a background theme I personally am associated with surfing and beach activities, it would be great if this was able to be reflected in the design.
Thank you.

```html
<!DOCTYPE html>
<html lang="en">
<head>
<meta charset="utf-8">
<title>Mr Colin Brasket – Podiatric Foot &amp; Ankle Surgeon</title>
<link href="https://fonts.googleapis.com/css2?family=Ubuntu:wght@700&family=Arimo:wght@400;700&display=swap" rel="stylesheet">
<style>
:root{
  --navy:#1d3b6e;
  --orange:#e2601e;
  --text:#555;
  --muted:#888;
  --grey-bg:#dcdcdc;
  --panel-dark:#6f6f6a;
  --panel-light:#c9c9c9;
  --footer:#dedede;
  --green:#7cc41a;
  --blue:#1f7bc6;
}
*{box-sizing:border-box;margin:0;padding:0}
html,body{width:772px;height:1200px;overflow:hidden}
body{position:relative;background:#fff;font-family:Arimo,Arial,sans-serif;color:var(--text)}
.abs{position:absolute}
.top-bg{left:0;top:0;width:772px;height:450px}
.brand{left:72px;top:30px;display:flex;align-items:center;gap:8px;font-size:16px;font-weight:700;color:var(--navy)}
.brand .dot{width:24px;height:24px;border-radius:50%;background:var(--orange)}
.phone{left:388px;top:20px;font-size:15px;font-weight:700;color:#555}
.search{left:509px;top:14px;width:168px;height:26px;border:1px solid #ccc;border-radius:4px;background:linear-gradient(#fff,#ececec)}
.search svg{position:absolute;right:6px;top:6px}
.nav a{position:absolute;top:59px;font-size:9.5px;color:#444;text-decoration:none}
.nav .home{left:308px;top:54px;width:53px;height:19px;background:#fff;color:var(--navy);text-align:center;line-height:19px}
.slider{left:64px;top:95px;width:643px;height:317px;background:#fff;border-radius:6px;box-shadow:0 4px 10px rgba(0,0,0,.15)}
.slide{left:70px;top:100px;width:632px;height:306px;background:linear-gradient(180deg,#8fbde6 0%,#c9a98c 30%,#d9bfa0 60%,#cdb597 100%)}
.caption{left:89px;top:192px;width:348px;height:174px;background:rgba(120,110,100,.45)}
.caption h1{position:absolute;left:23px;top:30px;font-family:Ubuntu,sans-serif;font-size:27px;color:#fff}
.caption p{position:absolute;left:24px;top:70px;width:310px;font-size:8.5px;line-height:14px;color:#fff}
.cta{left:114px;top:303px;width:151px;height:47px;border-radius:6px;background:linear-gradient(#b6ec3a,#5ea812);border:2px solid #d9f79a;color:#133;font-weight:700;font-size:14px;line-height:15px;padding:6px 0 0 43px}
.cta svg{position:absolute;left:10px;top:-4px}
.dots{left:368px;top:429px;display:flex;gap:4px}
.dots i{width:6px;height:6px;border-radius:50%;background:var(--blue)}
.dots i:nth-child(2){background:#888}
.about-mark{left:72px;top:455px;width:16px;height:16px;border-radius:50%;background:var(--orange)}
h2{font-weight:400;font-size:14px;color:var(--navy)}
h2 span{color:var(--orange)}
.about h2{position:absolute;left:95px;top:466px}
.about p{position:absolute;left:70px;top:494px;width:634px;font-size:7.6px;line-height:11.6px;color:#666}
.about a{position:absolute;left:70px;top:554px;font-size:7.6px;color:var(--blue);text-decoration:none}
.sidebar{left:516px;top:585px;width:188px;height:455px;background:var(--panel-light)}
.sidebar .dark{position:absolute;left:0;top:0;width:188px;height:247px;background:var(--panel-dark)}
.ribbon{left:524px;top:598px;width:182px;height:34px;background:var(--orange);color:#fff;font-size:14px;line-height:34px;padding-left:10px;clip-path:polygon(6px 0,100% 0,100% 100%,6px 100%,0 50%)}
.side-note{left:533px;top:643px;width:160px;font-size:7.3px;line-height:9.5px;color:#fff}
.field{position:absolute;left:535px;width:151px;height:18px;background:#fff;border:1px solid #ddd;font-size:7.5px;color:#999;padding:4px 5px}
.field b{color:var(--orange);font-weight:400}
.select{left:535px;top:672px;width:55px;height:18px;background:#fff;font-size:7.5px;color:#999;padding:4px 5px}
.select i{position:absolute;right:0;top:0;width:18px;height:18px;background:#7d7d78}
.send{left:535px;top:788px;width:151px;height:22px;background:var(--orange);color:#fff;font-weight:700;font-size:13px;text-align:center;line-height:22px}
.callnow{left:512px;top:846px;width:64px;height:24px;background:var(--blue);color:#fff;font-size:9px;font-weight:700;line-height:24px;text-align:center;clip-path:polygon(0 0,100% 0,92% 50%,100% 100%,0 100%)}
.callnum{left:582px;top:849px;font-size:14px;color:#444}
.hours{left:580px;top:886px;font-size:7.5px;line-height:12.8px;color:#333}
.hours .open{color:var(--blue);font-weight:700;font-size:8.5px}
.eforms{left:549px;top:996px;width:113px;height:24px;border-radius:12px;background:linear-gradient(#fff,#e6e6e6);box-shadow:0 1px 3px rgba(0,0,0,.3);color:var(--blue);font-weight:700;font-size:13px;line-height:24px;padding-left:34px}
.eforms svg{position:absolute;left:12px;top:3px}
.col h2{position:absolute;top:600px}
.photo{position:absolute;top:623px;height:91px}
.post h3{position:absolute;font-size:9px;font-weight:400;color:#333}
.post p{position:absolute;font-size:7.2px;line-height:11.5px;color:#777;width:200px}
.post .meta{font-size:6.3px;color:#999}
.rule{position:absolute;height:1px;background:#e4e4e4}
.feature h2{position:absolute;left:64px;top:857px;line-height:19px}
.feature .intro{position:absolute;left:64px;top:913px;font-size:7.6px;line-height:11px;color:#222;width:190px}
.bullets{position:absolute;top:943px;font-size:7.6px;line-height:11px;color:#444;list-style:none}
.bullets li{padding-left:9px;position:relative}
.bullets li::before{content:"";position:absolute;left:0;top:3px;width:4px;height:4px;background:var(--blue)}
.viewall{position:absolute;top:1010px;font-size:7.6px;color:#333}
.banner{left:273px;top:902px;width:199px;height:90px;background:linear-gradient(90deg,#5b8fc0 0%,#bcd5ea 45%,#e7eff7 100%)}
.banner h4{position:absolute;left:61px;top:18px;font-weight:400;font-size:12px;letter-spacing:.5px;color:var(--navy);font-variant:small-caps}
.banner p{position:absolute;left:61px;top:34px;width:130px;font-size:6.6px;line-height:8px;color:#333}
.banner .more{position:absolute;right:6px;bottom:2px;width:64px;height:14px;background:#3d6a99;color:#fff;font-size:7.3px;font-weight:700;text-align:center;line-height:14px}
.footer{left:0;top:1044px;width:772px;height:156px;background:var(--footer)}
.site-footer h5{position:absolute;top:1066px;font-size:11px;font-weight:400;color:var(--navy)}
.footer-line{position:absolute;top:1076px;width:1px;height:108px;background:#ccc}
.sitemap{position:absolute;left:77px;top:1094px;font-size:6.8px;line-height:11.6px;color:#444;list-style:none}
.news{position:absolute;left:173px;font-size:6.6px;line-height:11px;color:#444}
.sub{position:absolute;left:312px;width:100px;height:16px;background:#fff;border:1px solid #ccc;font-size:6.5px;color:#999;padding:3px 5px}
.submit{left:312px;top:1135px;width:40px;height:15px;background:var(--blue);color:#fff;font-size:6.5px;font-weight:700;text-align:center;line-height:15px}
.map{left:446px;top:1097px;width:114px;height:53px;background:#e6e4df;border:1px solid #ccc}
.addr{left:446px;top:1159px;width:130px;font-size:6.6px;line-height:11px;color:#444}
.foot-brand{left:606px;top:1112px;display:flex;align-items:center;gap:5px;font-size:9.5px;font-weight:700;color:var(--navy)}
.foot-brand .dot{width:14px;height:14px;border-radius:50%;background:var(--orange)}
</style>
</head>
<body>
<svg class="abs top-bg" viewBox="0 0 772 450" aria-hidden="true"><defs><linearGradient id="tg" x1="0" y1="0" x2="0" y2="1"><stop offset="0" stop-color="#d6d6d6"/><stop offset="1" stop-color="#e9e9e9"/></linearGradient></defs><path d="M0 0H772V312Q520 330 420 445H0Z" fill="url(#tg)"/></svg>

<header>
  <div class="abs brand"><span class="dot"></span>Mr Colin Brasket</div>
  <div class="abs phone">+08 9012 3456</div>
  <div class="abs search"><svg width="12" height="12" viewBox="0 0 12 12"><circle cx="5" cy="5" r="3.5" fill="none" stroke="#333" stroke-width="1.4"/><path d="M7.5 7.5L11 11" stroke="#333" stroke-width="1.8"/></svg></div>
  <nav class="nav">
    <a class="home">Home</a>
    <a style="left:376px">About</a>
    <a style="left:434px">Services</a>
    <a style="left:502px">Location</a>
    <a style="left:571px">Specialist</a>
    <a style="left:645px">Contact</a>
  </nav>
</header>

<section>
  <div class="abs slider"></div>
  <div class="abs slide" role="img" aria-label="Photo of bare feet resting in beach sand under a blue sky"></div>
  <div class="abs caption">
    <h1>Healthy Ankle Life</h1>
    <p>simply dummy text of the printing and typesetting industry. Lorem Ipsum has been the industry's standard dummy text ever since the 1500s,</p>
  </div>
  <div class="abs cta"><svg width="30" height="40" viewBox="0 0 30 40"><path d="M8 0H22V20H30L15 38L0 20H8Z" fill="#e8f0a0" stroke="#8cb91e"/></svg>Request<br>Appointment</div>
  <div class="abs dots"><i></i><i></i><i></i></div>
</section>

<section class="about">
  <div class="abs about-mark"></div>
  <h2><span>About</span> Mr. Colin Brasket</h2>
  <p>Vestibulum rutrum pharetra diam, eget dapibus leo vehicula ut. Fusce aliquam, odio eget adipiscing lobortis.Vestibulum rutrum pharetra diam, eget dapibus leo vehicula ut. Fusce aliquam, odio eget adipiscing lobortis.Vestibulum rutrum pharetra diam, eget dapibus leo vehicula ut. Fusce aliquam, odio eget adipiscing lobortis.Vestibulum rutrum pharetra diam, eget dapibus leo vehicula ut. Fusce aliquam, odio eget adipiscing lobortis.Vestibulum rutrum pharetra diam, eget dapibus leo vehicula ut. Fusce aliquam, odio eget adipiscing lobortis.Vestibulum rutrum pharetra diam, eget dapibus leo vehicula ut. Fusce aliquam, odio eget adipiscing lobortis.Vestibulum rutrum pharetra diam, eget dapibus leo vehicula ut. Fusce aliquam, odio eget adipiscing lobortis.</p>
  <a>[ read More + ]</a>
</section>

<div class="rule" style="left:64px;top:585px;width:452px"></div>

<section class="col">
  <h2 style="left:64px"><span>Surgical</span> Fellowships</h2>
  <div class="photo" style="left:64px;width:202px;background:linear-gradient(135deg,#8a7a5a,#c4a89a 40%,#6aa0d0 70%,#e8e8e8)" role="img" aria-label="Photo of a surgeon in blue gloves dressing a foot"></div>
  <div class="post">
    <h3 style="left:65px;top:722px">Pellentesque convallis tellus at turpis</h3>
    <p style="left:65px;top:741px">Pellentesque convallis tellus at turpis dignissim sit amet cursus erat consectetur. Morbi non neque</p>
    <div class="rule" style="left:64px;top:770px;width:198px"></div>
    <h3 style="left:65px;top:779px">Nullam dapibus neque aliquam quam</h3>
    <p style="left:65px;top:797px">Nullam dapibus neque aliquam quam porta sit amet tempor felis mattis. Nullam non elit lectus, sit amet</p>
  </div>
  <h2 style="left:273px"><span>Training</span> Program Undertaken</h2>
  <div class="photo" style="left:274px;width:200px;background:linear-gradient(180deg,#d6d6d6,#c9b8a8 60%,#b8a290)" role="img" aria-label="Photo of a foot wearing a white ankle brace"></div>
  <div class="post">
    <h3 style="left:275px;top:722px">Pellentesque convallis tellus at turpis</h3>
    <p class="meta" style="left:275px;top:741px">March 29, 2013 &nbsp;| &nbsp;<span style="color:var(--blue)">4 Comments</span></p>
    <p style="left:275px;top:752px">Pellentesque convallis tellus at turpis dignissim</p>
    <div class="rule" style="left:274px;top:770px;width:198px"></div>
    <h3 style="left:275px;top:779px">Nullam dapibus neque aliquam quam</h3>
    <p class="meta" style="left:275px;top:797px">March 29, 2013 &nbsp;| &nbsp;<span style="color:var(--blue)">No Comments</span></p>
    <p style="left:275px;top:808px">Nullam dapibus neque aliquam quam porta sit amet tempor</p>
  </div>
</section>

<section class="feature">
  <h2><span>Our Feature</span><br>Services</h2>
  <div class="rule" style="left:64px;top:901px;width:186px;background:#ccc"></div>
  <p class="intro">At vero eos et accusamus et iusto odio dignissimos ducimus.</p>
  <ul class="bullets" style="left:66px;width:85px"><li>Soothing Sedation</li><li>Beautiful Porcelain Veneers</li><li>Easy Invisable Braces</li></ul>
  <ul class="bullets" style="left:154px;width:100px"><li>Mini Dental Implants</li><li>Brilliant Teeth Whitening</li><li>Safe Digital X-Rays</li></ul>
  <span class="viewall" style="left:66px">View All</span>
  <h2 style="left:273px"><span>Innovative</span><br>Products</h2>
  <div class="abs banner" role="img" aria-label="Sports medicine banner with a woman holding her ankle">
    <h4>Sports Medicine</h4>
    <p>We specialize in the prevention and treatment of injuries associated with athletic and active individuals.</p>
    <span class="more">Read More</span>
  </div>
  <span class="viewall" style="left:274px">View All</span>
</section>

<aside>
  <div class="abs sidebar"><div class="dark"></div></div>
  <div class="abs ribbon">Send Your Health History</div>
  <p class="abs side-note">You can find the full contact form under the "Contact us" menu!</p>
  <div class="abs select">Title<i><svg width="18" height="18" viewBox="0 0 18 18"><path d="M5 7L9 11L13 7" stroke="#fff" stroke-width="1.6" fill="none"/></svg></i></div>
  <div class="field" style="top:696px">First name<b>*</b></div>
  <div class="field" style="top:719px">Surname<b>*</b></div>
  <div class="field" style="top:742px;height:41px">Your health details<b>*</b></div>
  <div class="abs send">Send Now!</div>
  <div class="abs callnow">CALL NOW!</div>
  <div class="abs callnum">(123)-456-789</div>
  <div class="abs hours"><span class="open">Open :</span><br><b>Monday - Friday:</b><br>By Appointment Only<br><b>Saturday:</b><br>By Appointment Only<br><b>Sunday (seasonal):</b><br>Closed</div>
  <div class="abs eforms"><svg width="18" height="18" viewBox="0 0 18 18"><rect x="2" y="2" width="12" height="15" fill="#fff" stroke="#777"/><path d="M5 7H11M5 10H11M5 13H9" stroke="#999"/><path d="M10 12L16 3" stroke="#e2601e" stroke-width="2"/></svg>E-Forms</div>
</aside>

<footer class="site-footer">
  <div class="abs footer"></div>
  <h5 style="left:76px">Site Map</h5>
  <h5 style="left:172px">Follow with us</h5>
  <h5 style="left:311px">Subscribe</h5>
  <h5 style="left:445px">Location</h5>
  <h5 style="left:606px">Copyright</h5>
  <div class="footer-line" style="left:154px"></div>
  <div class="footer-line" style="left:294px"></div>
  <div class="footer-line" style="left:430px"></div>
  <div class="footer-line" style="left:588px"></div>
  <ul class="sitemap"><li>Home</li><li>Meet the Doctor</li><li>Our Office</li><li>Services</li><li>Smile Gallery</li><li>Patient Resources</li><li>Contact Us</li></ul>
  <p class="news" style="top:1094px">12/07/2013<br>is simply dummy text of the</p>
  <p class="news" style="top:1140px">12/07/2013<br>is simply dummy text of the</p>
  <div class="sub" style="top:1097px">Enter Your Name</div>
  <div class="sub" style="top:1115px">Enter Your Email ID</div>
  <div class="abs submit">SUBMIT</div>
  <div class="abs map" role="img" aria-label="Street map of the practice location"></div>
  <p class="abs addr">2140 N Harbor Ln #210 Coralton, TN 38000</p>
  <div class="abs foot-brand"><span class="dot"></span>Mr Colin Brasket</div>
</footer>
</body>
</html>
```